Accountability Project Graphics

I want to create 10 social media graphics (new Instagram size 4:5 (1080 x 1350 pixels) focusing on our Quilvo Accountability App, using any of the 3 pictures attached. Use the attached pics only, NO RANDOM STOCK PHOTOGRAPHY. For the color scheme, use the landing page colors/fonts (attached).
You can add any of the 3 photos attached but I mainly need BOLD text that includes these headlines and sub-headlines on them.
Please NOTE for all the headlines below, also add this sub-headline on each graphic:
Stay Consistent with RT in Your Pocket!
Here are the headlines:
• Stop Starting Over Every Monday
• You don't need more willpower. You need more support
• Built for women who are tired of doing this alone
• When Motivation Fades, RT Checks In
• The Support System You've Been Missing
• Support When Motivation Disappears
• What if RT Checked in Every Day?
• The Missing Piece Isn't Another Diet
• Eat the food you love. Stay accountable every day.
• One Bad Meal Doesn't Mean You Failed
women over 40 trying to lose weight

```html
<!DOCTYPE html>
<html lang="en">
<head>
<meta charset="utf-8">
<title>Quilvo Accountability App – Social Graphics</title>
<link rel="stylesheet" href="https://fonts.googleapis.com/css2?family=Abril+Fatface&family=Archivo+Black&family=Yellowtail&family=Oswald:wght@300;600&display=swap">
<style>
  :root {
    --pink: #ec3a85;
    --pink-hot: #f2478d;
    --pink-soft: #f7a9c8;
    --pink-pale: #fde4ee;
    --ink: #0e1422;
    --white: #ffffff;
    --serif: "Abril Fatface", Georgia, serif;
    --block: "Archivo Black", Arial, sans-serif;
    --script: "Yellowtail", cursive;
    --cond: "Oswald", "Arial Narrow", sans-serif;
  }
  * { margin: 0; padding: 0; box-sizing: border-box; }
  html, body { width: 1200px; height: 975px; overflow: hidden; background: var(--white); }
  .sheet { position: relative; width: 1200px; height: 975px; }
  .post { position: absolute; width: 340px; height: 424px; overflow: hidden; }
  .post--stop { left: 43px; top: 30px; }
  .post--willpower { left: 427px; top: 30px; }
  .post--women { left: 811px; top: 30px; }
  .post--motivation { left: 195px; top: 494px; }
  .post--motivation-photo { left: 597px; top: 494px; }
  .post__bg { position: absolute; inset: 0; }
  .line { position: absolute; line-height: 1; white-space: nowrap; }
  .serif { font-family: var(--serif); }
  .block { font-family: var(--block); }
  .script { font-family: var(--script); }
  .ink { color: var(--ink); }
  .white { color: var(--white); }
  .pink { color: var(--pink); }
  .center { left: 0; width: 100%; text-align: center; }
  .photo { position: absolute; }
  .photo--coach { background: linear-gradient(180deg, #2a1c22 0%, #111116 35%, #0b0b0e 100%); border-radius: 80px 60px 0 0; }
  .photo--hug { background: linear-gradient(135deg, #3a2422 0%, #e34e8a 45%, #f6b8cf 100%); border-radius: 70px 0 0 0; }
  .tagline { position: absolute; font-family: var(--cond); color: var(--white); font-size: 17px; line-height: 1.3; }
  .tagline b { font-weight: 600; }
  .tagline span { font-weight: 300; }
  .pill { display: inline-block; background: var(--pink); color: var(--white); border-radius: 14px; padding: 3px 16px 4px; font-family: var(--serif); font-size: 22px; }
</style>
</head>
<body>
<svg width="0" height="0" style="position:absolute" aria-hidden="true">
  <defs>
    <linearGradient id="outerGrad" x1="0" y1="0" x2="0" y2="1">
      <stop offset="0" stop-color="#f58ab5"/>
      <stop offset="1" stop-color="#fbd0e0"/>
    </linearGradient>
    <linearGradient id="cardGrad" x1="0" y1="0" x2="0.3" y2="1">
      <stop offset="0" stop-color="#f6529a"/>
      <stop offset="0.45" stop-color="#fba9c8"/>
      <stop offset="0.8" stop-color="#fff3f7"/>
      <stop offset="1" stop-color="#ffffff"/>
    </linearGradient>
    <linearGradient id="bandGrad" x1="0" y1="0" x2="1" y2="0">
      <stop offset="0" stop-color="#e8327e"/>
      <stop offset="1" stop-color="#f04d92"/>
    </linearGradient>
  </defs>
</svg>

<main class="sheet">

  <!-- Stop Starting Over -->
  <section class="post post--stop">
    <svg class="post__bg" viewBox="0 0 340 424" aria-hidden="true">
      <rect width="340" height="424" fill="url(#outerGrad)"/>
      <rect x="8" y="18" width="290" height="420" rx="22" fill="url(#cardGrad)"/>
      <polygon points="0,364 340,305 340,424 0,424" fill="url(#bandGrad)"/>
      <polygon points="0,364 340,305 340,309 0,368" fill="#f56aa4"/>
      <path d="M22 328 Q50 305 135 312" stroke="var(--pink)" stroke-width="6" fill="none" stroke-linecap="round"/>
      <circle cx="137" cy="313" r="2" fill="var(--pink)"/>
    </svg>
    <div class="photo photo--coach" style="left:205px;top:38px;width:135px;height:386px" role="img" aria-label="Coach smiling, standing with hand on hip, dressed in black"></div>
    <div class="line serif ink" style="left:18px;top:52px;font-size:60px">STOP</div>
    <div class="line block white" style="left:19px;top:116px;font-size:26px">STARTING</div>
    <div class="line block ink" style="left:18px;top:150px;font-size:47px">OVER</div>
    <div class="line block pink" style="left:19px;top:202px;font-size:43px">EVERY</div>
    <div class="line script pink" style="left:22px;top:255px;font-size:52px">Monday</div>
    <p class="tagline" style="left:21px;top:372px"><b>Stay Consistent with RT</b><br><span>in Your Pocket!</span></p>
  </section>

  <!-- More Support -->
  <section class="post post--willpower">
    <svg class="post__bg" viewBox="0 0 340 424" aria-hidden="true">
      <rect width="340" height="424" fill="url(#outerGrad)"/>
      <rect x="14" y="16" width="312" height="420" rx="22" fill="url(#cardGrad)"/>
      <polygon points="0,376 340,332 340,424 0,424" fill="url(#bandGrad)"/>
      <polygon points="0,376 340,332 340,336 0,380" fill="#f56aa4"/>
      <path d="M102 354 Q135 332 225 334" stroke="var(--pink)" stroke-width="6" fill="none" stroke-linecap="round"/>
      <circle cx="228" cy="335" r="2" fill="var(--pink)"/>
    </svg>
    <div class="line serif ink center" style="top:60px;font-size:43px">YOU DON'T</div>
    <div class="line center white" style="top:110px;font-size:35px"><span class="script">Need</span> <span class="serif">MORE</span></div>
    <div class="line block ink center" style="top:160px;font-size:30px">WILLPOWER.</div>
    <div class="line block pink center" style="top:203px;font-size:29px">YOU NEED</div>
    <div class="line center" style="top:242px"><span class="pill">MORE</span></div>
    <div class="line script pink center" style="top:272px;font-size:48px">Support</div>
    <p class="tagline center" style="top:396px"><b>Stay Consistent with RT</b> <span>in Your Pocket!</span></p>
  </section>

  <!-- Built for Women -->
  <section class="post post--women">
    <svg class="post__bg" viewBox="0 0 340 424" aria-hidden="true">
      <rect width="340" height="424" fill="url(#outerGrad)"/>
      <rect x="10" y="18" width="320" height="420" rx="22" fill="url(#cardGrad)"/>
      <polygon points="0,346 340,300 340,424 0,424" fill="url(#bandGrad)"/>
      <polygon points="0,346 340,300 340,304 0,350" fill="#f56aa4"/>
      <path d="M22 310 Q60 275 165 265" stroke="var(--pink)" stroke-width="6" fill="none" stroke-linecap="round"/>
    </svg>
    <div class="photo photo--hug" style="left:164px;top:176px;width:176px;height:248px" role="img" aria-label="Two women sharing a joyful hug"></div>
    <div class="line serif ink" style="left:22px;top:20px;font-size:86px">BUILT</div>
    <div class="line white" style="left:24px;top:104px;font-size:44px"><span class="script">for</span> <span class="serif">WOMEN</span></div>
    <div class="line block ink" style="left:22px;top:156px;font-size:21px;letter-spacing:1px">WHO ARE TIRED OF</div>
    <div class="line block pink" style="left:22px;top:185px;font-size:21px;letter-spacing:1px">DOING THIS</div>
    <div class="line script pink" style="left:24px;top:206px;font-size:58px">Alone</div>
    <p class="tagline" style="left:16px;top:348px"><b>Stay Consistent with RT</b><br><span>in Your Pocket!</span></p>
  </section>

  <!-- RT Checks In -->
  <section class="post post--motivation">
    <svg class="post__bg" viewBox="0 0 340 424" aria-hidden="true">
      <rect width="340" height="424" fill="url(#outerGrad)"/>
      <rect x="14" y="16" width="312" height="420" rx="22" fill="url(#cardGrad)"/>
      <polygon points="0,382 340,334 340,424 0,424" fill="url(#bandGrad)"/>
      <polygon points="0,382 340,334 340,338 0,386" fill="#f56aa4"/>
      <path d="M108 358 Q140 335 212 334" stroke="var(--pink)" stroke-width="6" fill="none" stroke-linecap="round"/>
      <circle cx="213" cy="339" r="2" fill="var(--pink)"/>
    </svg>
    <div class="line script ink center" style="top:22px;font-size:36px">When</div>
    <div class="line serif white center" style="top:65px;font-size:31px">MOTIVATION</div>
    <div class="line block ink center" style="top:100px;font-size:57px">FADES,</div>
    <div class="line block pink center" style="top:160px;font-size:140px;letter-spacing:-4px">RT</div>
    <div class="line center" style="top:290px;font-size:40px"><span class="script pink">Checks</span> <span class="block ink" style="font-size:30px">IN</span></div>
    <p class="tagline center" style="top:396px"><b>Stay Consistent with RT</b> <span>in Your Pocket!</span></p>
  </section>

  <!-- RT Checks In with coach -->
  <section class="post post--motivation-photo">
    <svg class="post__bg" viewBox="0 0 340 424" aria-hidden="true">
      <rect width="340" height="424" fill="url(#outerGrad)"/>
      <rect x="14" y="16" width="310" height="420" rx="22" fill="url(#cardGrad)"/>
      <polygon points="0,369 340,340 340,424 0,424" fill="url(#bandGrad)"/>
      <polygon points="0,369 340,340 340,344 0,373" fill="#f56aa4"/>
      <path d="M34 362 Q70 340 155 345" stroke="var(--pink)" stroke-width="6" fill="none" stroke-linecap="round"/>
      <circle cx="157" cy="345" r="2" fill="var(--pink)"/>
    </svg>
    <div class="photo photo--coach" style="left:210px;top:10px;width:130px;height:414px" role="img" aria-label="Coach smiling, standing with hand on hip, dressed in black"></div>
    <div class="line script ink" style="left:0;width:250px;text-align:center;top:33px;font-size:36px">When</div>
    <div class="line serif ink" style="left:0;width:250px;text-align:center;top:77px;font-size:30px">MOTIVATION</div>
    <div class="line block ink" style="left:20px;top:112px;font-size:46px">FADES</div>
    <div class="line block pink" style="left:20px;top:172px;font-size:124px;letter-spacing:-4px;text-shadow:4px 3px 0 var(--ink)">RT</div>
    <div class="line" style="left:22px;top:291px;font-size:40px"><span class="script pink">Checks</span> <span class="block ink" style="font-size:30px">IN</span></div>
    <p class="tagline" style="left:22px;top:374px"><b>Stay Consistent with RT</b><br><span>in Your Pocket!</span></p>
  </section>

</main>
</body>
</html>
```